Business card design for web travel company

Hi
we'd like to receive some proposal for a business card design.
Stayvora is a private travel club, dedicated to all travel lovers, with unique offers for exclusive destinations all around the world. At Stayvora you can find a wide range of offers for resorts, boutique hotels and travel packages at the best guaranteed price available on the market. The convenience of the offer is guaranteed by a private sales model: offers are available for a limited time only and they are personally chosen by Stayvora's qualified team of travel experts.
We offer only exclusive hotels with discounted prices but we are not an outlet or a discount supermarket: the design should reflect our connection with luxury, exclusivity using the same style of our website www.stayvora-example.com.
We want to make sure that when we'll present ourself to our business partner they will feel immediately which is our brand positioning giving them also a sense of an affordable and reliable partner.
In attachment you can also find our brand guidelines (please note that we are NOT USING ANY MORE THE TAG LINE "Five star outlet" mentioned in it).
The info to be inserted are:
Name Surname
Job Title
Tel
Mobile (when needed)
Email
Stayvora S.r.l.
Via Bruno Salvi 27
20139 Milano

```html
<!DOCTYPE html>
<html lang="en">
<head>
<meta charset="utf-8">
<title>Stayvora business card</title>
<link rel="stylesheet" href="https://fonts.googleapis.com/css2?family=Arimo:wght@400;700&family=Questrial&display=swap">
<style>
  :root {
    --backdrop: #ecebe8;
    --card-white: #ffffff;
    --card-black: #000000;
    --ink: #111111;
    --gold: #b4a57a;
    --band: #857d5a;
    --web-grey: #cfcfcf;
  }
  * { margin: 0; padding: 0; box-sizing: border-box; }
  html, body { width: 1200px; height: 900px; overflow: hidden; }
  body {
    background: var(--backdrop);
    font-family: "Arimo", Arial, sans-serif;
    color: var(--ink);
    position: relative;
  }
  .card {
    position: absolute;
    top: 300px;
    width: 523px;
    height: 300px;
    overflow: hidden;
  }
  .card--front {
    left: 60px;
    background: var(--card-white);
    border-radius: 12px 0 0 12px;
    box-shadow: 0 1px 3px rgba(0,0,0,.18);
  }
  .card--back {
    left: 617px;
    background: var(--card-black);
    border-radius: 0 12px 12px 0;
    box-shadow: 0 1px 3px rgba(0,0,0,.25);
  }
  .card__band {
    position: absolute;
    top: 0;
    width: 20px;
    height: 100%;
    background: var(--band);
  }
  .card--front .card__band { right: 0; }
  .card--back .card__band { left: 0; }

  .wordmark {
    position: absolute;
    font-family: "Arimo", Arial, sans-serif;
    font-weight: 400;
    font-size: 46px;
    letter-spacing: -0.5px;
    line-height: 1;
    display: flex;
    align-items: center;
    gap: 10px;
  }
  .wordmark__square {
    width: 12px;
    height: 12px;
    background: var(--gold);
  }
  .card--front .wordmark { left: 28px; top: 130px; color: var(--ink); }
  .card--back .wordmark { left: 46px; top: 126px; color: #ffffff; }

  .contact {
    position: absolute;
    left: 283px;
    top: 110px;
    font-size: 12.5px;
    line-height: 19px;
  }
  .contact__name {
    font-weight: 700;
    font-size: 18px;
    line-height: 24px;
    margin-bottom: 2px;
  }
  .contact__row {
    display: flex;
    align-items: center;
    gap: 4px;
    margin-top: 2px;
  }
  .contact__row--first { margin-top: 4px; }
  .contact__icon { width: 14px; height: 11px; flex: none; }
  .contact__address { font-size: 12px; line-height: 19px; }

  .website {
    position: absolute;
    right: 20px;
    top: 143px;
    font-family: "Questrial", Arial, sans-serif;
    font-size: 14px;
    letter-spacing: 1px;
    color: var(--web-grey);
  }
</style>
</head>
<body>
  <section class="card card--front" aria-label="Card front">
    <div class="wordmark">Stayvora<span class="wordmark__square"></span></div>
    <div class="contact">
      <p class="contact__name">Lorenzo Castelli</p>
      <p class="contact__address">Stayvora S.r.l.</p>
      <p class="contact__address">Via Bruno Salvi 27 20139 Milano</p>
      <p class="contact__row contact__row--first">
        <svg class="contact__icon" viewBox="0 0 14 11" aria-hidden="true">
          <path d="M1 4 Q7 -1 13 4 L11 5.5 L9.5 3.8 L4.5 3.8 L3 5.5 Z" fill="var(--gold)"/>
          <rect x="3" y="5.5" width="8" height="5" rx="1" fill="var(--gold)"/>
        </svg>
        <span>: +23 4417 2290</span>
      </p>
      <p class="contact__row">
        <svg class="contact__icon" viewBox="0 0 14 11" aria-hidden="true">
          <rect x="1" y="1" width="12" height="9" fill="none" stroke="var(--gold)" stroke-width="1.4"/>
          <path d="M1 1 L7 6 L13 1" fill="none" stroke="var(--gold)" stroke-width="1.4"/>
        </svg>
        <span>: lorenzo@stayvora-example.com</span>
      </p>
    </div>
    <div class="card__band"></div>
  </section>

  <section class="card card--back" aria-label="Card back">
    <div class="card__band"></div>
    <div class="wordmark">Stayvora<span class="wordmark__square"></span></div>
    <p class="website">www.stayvora-example.com</p>
  </section>
</body>
</html>
```